Vellmore Family Law, legal technician needs a website and design

I need a website for a family law practice. I specialize in collaborative law, unbundled services, and mediation. The website must contain my company logo (file attached), and the website must be a mixture of my personality and my profession. I have attached additional information to explain my personality and profession.

Target Market(s)

Lower through middle-class (income level up to $200,000 per year)

Coding

Coded - Design and coding required

Number of Pages Required

1 page

Requirements
Must have
• Must have enough pages to cover required content. I submitted below some content about the collaborative law process. All of the content is not necessary. However, the website must have enough content to clearly describe the services I offer. Use your professionalism and judgment regarding font, font size, etc.

```html
<!DOCTYPE html>
<html lang="en">
<head>
<meta charset="utf-8">
<title>Vellmore Family Law</title>
<link href="https://fonts.googleapis.com/css2?family=Crimson+Pro:wght@400;500&family=Lato:wght@400;700&display=swap" rel="stylesheet">
<style>
:root{
  --navy:#03052e;
  --gold:#b7b33a;
  --gold-dark:#8f8a2c;
  --olive:#7a6e2c;
  --blush:#f3eeee;
  --ink:#1c1c28;
  --text:#3d3d46;
  --white:#ffffff;
  --serif:'Crimson Pro', Georgia, serif;
  --sans:'Lato', Arial, sans-serif;
}
*{box-sizing:border-box;margin:0;padding:0}
html,body{width:1200px;height:4721px;overflow:hidden}
body{position:relative;font-family:var(--sans);color:var(--text);background:var(--white)}
.abs{position:absolute}
.btn{position:absolute;display:flex;align-items:center;justify-content:center;background:var(--gold);color:var(--white);font:700 12px var(--sans);letter-spacing:.5px;border-radius:18px;height:34px}
.section-title{position:absolute;left:0;width:1200px;text-align:center;font:400 33px var(--serif);color:var(--ink)}
.rule{position:absolute;width:56px;height:2px;background:var(--gold)}
.brand{position:absolute;display:flex;align-items:center;gap:14px}
.brand-mark{width:40px;height:40px;border:2px solid var(--gold)}
.brand-name{font:500 26px var(--serif);color:var(--gold);line-height:1}

/* header */
.site-header{left:0;top:0;width:1200px;height:123px;background:var(--navy)}
.nav a{position:absolute;top:80px;font:400 17px var(--serif);color:var(--white);text-decoration:none}
.nav a.active{color:var(--gold)}
.call{position:absolute;left:936px;top:24px;color:var(--white)}
.call small{display:block;font:400 13px var(--serif)}
.call strong{font:400 20px var(--serif)}
.call-icon{position:absolute;left:893px;top:30px}

/* hero */
.hero{left:0;top:123px;width:1200px;height:577px;background:linear-gradient(100deg,#e9e4dd 0%,#d9c8b3 35%,#c79a6c 55%,#8d7460 75%,#d8d2cb 100%)}
.hero h1{position:absolute;left:0;top:40px;width:1200px;text-align:center;font:400 29px/36px var(--serif);color:var(--ink)}
.arrow-circle{position:absolute;width:38px;height:38px;border:2px solid var(--ink);border-radius:10px;display:flex;align-items:center;justify-content:center}

/* services */
.service-card{position:absolute;width:310px;height:460px}
.service-photo{position:absolute;left:0;top:0;width:297px;height:248px;border-radius:10px}
.service-box{position:absolute;left:15px;top:171px;width:295px;height:289px;border:1.5px solid var(--gold);border-radius:14px}
.service-card h3{position:absolute;left:15px;top:280px;width:295px;text-align:center;font:400 21px var(--serif);color:var(--ink)}
.service-card p{position:absolute;left:35px;top:320px;width:255px;text-align:center;font:400 13px/19px var(--sans);color:var(--text)}

/* welcome */
.welcome{left:0;top:1369px;width:1200px;height:503px;background:var(--blush)}
.welcome-mark{position:absolute;left:152px;top:65px;width:380px;height:380px;display:flex;align-items:center;justify-content:center;flex-direction:column;gap:18px}
.welcome-mark .sq{width:70px;height:70px;background:var(--gold)}
.welcome-mark span{font:500 54px var(--serif);color:var(--gold-dark)}
.welcome .eyebrow{position:absolute;left:597px;top:46px;font:400 20px var(--serif);color:var(--ink)}
.welcome h2{position:absolute;left:597px;top:76px;font:400 34px var(--serif);color:var(--ink)}
.welcome p{position:absolute;left:597px;top:168px;width:460px;font:400 14.5px/23.2px var(--sans);color:var(--text)}

/* testimonials */
.testimonials{left:0;top:1872px;width:1200px;height:579px;background:var(--navy)}
.testimonials .section-title{color:var(--white);top:48px}
.quote-card{position:absolute;top:187px;width:295px;height:323px;border:1.5px solid var(--gold);border-radius:8px}
.quote-mark{position:absolute;left:122px;top:-18px;width:50px;background:var(--navy);text-align:center;font:700 44px/40px var(--serif);color:var(--gold)}
.quote-card p{position:absolute;left:30px;top:44px;width:235px;text-align:center;font:400 14px/22px var(--sans);color:#d8d8e0}
.quote-card .rule{left:120px;top:252px}
.quote-card cite{position:absolute;left:0;top:273px;width:295px;text-align:center;font:400 16px var(--serif);font-style:normal;color:var(--gold)}

/* articles */
.article{position:absolute;top:2607px;width:452px;height:480px}
.article-photo{position:absolute;left:0;top:0;width:452px;height:304px;border-radius:10px}
.article-box{position:absolute;left:22px;top:238px;width:407px;height:242px;background:var(--olive);border-radius:10px}
.article-box h3{position:absolute;left:40px;top:32px;width:330px;font:400 21px/26px var(--serif);color:#f1efe0}
.article-box p{position:absolute;left:40px;top:96px;width:320px;font:400 13.5px/19px var(--sans);color:#ece9d6}

/* video */
.video{left:0;top:3254px;width:1200px;height:538px;background:linear-gradient(120deg,#d8d9dc 0%,#eeeff1 40%,#e2e3e6 60%,#b9bcc2 100%)}
.play{position:absolute;left:583px;top:252px}
.video span{position:absolute;left:0;top:333px;width:1200px;text-align:center;font:400 18px var(--serif);color:var(--ink)}

/* contact */
.contact{left:0;top:3792px;width:1200px;height:586px;background:linear-gradient(180deg,#f3f1ef 0%,#ebe7e3 100%)}
.form{position:absolute;left:313px;top:152px;width:574px;height:376px;background:var(--white);border-radius:6px}
.field{position:absolute;border:1px solid #b9b9b9;border-radius:8px;font:400 12px var(--sans);color:#444;padding:14px 16px}

/* footer */
.site-footer{left:0;top:4378px;width:1200px;height:343px;background:var(--navy);color:var(--white)}
.site-footer h4{position:absolute;top:55px;font:700 12px var(--sans);letter-spacing:.5px}
.menu-list{position:absolute;left:456px;top:88px;list-style:none;font:400 11.5px/19.6px var(--sans)}
.info{position:absolute;display:flex;gap:10px;font:400 11px/14px var(--sans)}
.info .dot{width:24px;height:24px;border-radius:50%;background:var(--white);flex:none;display:flex;align-items:center;justify-content:center}
.copyright{position:absolute;left:0;top:4675px;width:1200px;text-align:center;font:400 9px var(--sans);color:#cfd0dc}
</style>
</head>
<body>

<header class="abs site-header">
  <div class="brand" style="left:134px;top:38px">
    <div class="brand-mark"></div>
    <div class="brand-name">Vellmore</div>
  </div>
  <svg class="call-icon" width="28" height="28" viewBox="0 0 24 24" fill="none" stroke="#fff" stroke-width="1.6"><path d="M5 3h4l2 5-2.5 1.5a11 11 0 0 0 6 6L16 13l5 2v4a2 2 0 0 1-2 2A16 16 0 0 1 3 5a2 2 0 0 1 2-2z"/></svg>
  <div class="call"><small>Call Us</small><strong>555.014.2290</strong></div>
  <nav class="nav">
    <a class="active" style="left:425px">Home</a>
    <a style="left:518px">About Us</a>
    <a style="left:641px">Services</a>
    <a style="left:755px">Blog</a>
    <a style="left:839px">Testimonials</a>
    <a style="left:980px">Contact us</a>
  </nav>
</header>

<section class="abs hero" role="img" aria-label="Family of four lying on the floor reading a book together">
  <h1>Vellmore Family Law, collaborative law and unbundled<br>legal services in King County, Washington state</h1>
  <div class="btn" style="left:535px;top:138px;width:128px">READ MORE</div>
  <div class="arrow-circle" style="left:65px;top:246px"><svg width="12" height="12" viewBox="0 0 12 12"><path d="M8 1 3 6l5 5" stroke="#1c1c28" stroke-width="2" fill="none"/></svg></div>
  <div class="arrow-circle" style="left:1120px;top:246px"><svg width="12" height="12" viewBox="0 0 12 12"><path d="m4 1 5 5-5 5" stroke="#1c1c28" stroke-width="2" fill="none"/></svg></div>
</section>

<h2 class="section-title" style="top:743px">Our Services</h2>

<div class="service-card" style="left:115px;top:837px">
  <div class="service-box"></div>
  <div class="service-photo" role="img" aria-label="Couple and advisors reviewing papers around a table" style="background:linear-gradient(135deg,#a88b6a,#d8c9b4 60%,#8a7a6a)"></div>
  <h3>Collaborative law</h3>
  <p>Every year, hundreds of thousands of marriages end in divorce. Are you in this situation right now?</p>
  <div class="btn" style="left:104px;top:406px;width:104px;height:30px;font-size:11px">READ MORE</div>
</div>
<div class="service-card" style="left:443px;top:837px">
  <div class="service-box"></div>
  <div class="service-photo" role="img" aria-label="Lawyer meeting a client across a desk" style="background:linear-gradient(135deg,#3f4a58,#8897a6 55%,#5c6672)"></div>
  <h3>Unbundled services</h3>
  <p>Lawyer and client contract for specific and limited legal services without the lawyer being responsible</p>
  <div class="btn" style="left:104px;top:406px;width:104px;height:30px;font-size:11px">READ MORE</div>
</div>
<div class="service-card" style="left:777px;top:837px">
  <div class="service-box"></div>
  <div class="service-photo" role="img" aria-label="Handshake over a desk with documents" style="background:linear-gradient(135deg,#3b3026,#b58a5a 55%,#e8dccb)"></div>
  <h3>Mediation</h3>
  <p>Mediation describes a consensual dispute resolution process in which the parties meet with a trained Mediator to resolve disputes.</p>
  <div class="btn" style="left:104px;top:406px;width:104px;height:30px;font-size:11px">READ MORE</div>
</div>

<section class="abs welcome">
  <div class="welcome-mark"><div class="sq"></div><span>Vellmore</span></div>
  <div class="eyebrow">Welcome to</div>
  <h2>Vellmore Family Law</h2>
  <div class="rule" style="left:597px;top:130px;width:88px;height:1.5px"></div>
  <p>There are many variations of passages of Lorem Ipsum available, but the majority have suffered alteration in some form, by injected humour, or randomised words which don't look even slightly believable. If you are going to use a passage of Lorem Ipsum, you need to be sure there isn't anything embarrassing hidden in the middle of text. All the Lorem Ipsum generators on the Internet tend to repeat predefined chunks as necessary, making this the first true generator on the Internet. It uses a dictionary of over 200 Latin words, combined</p>
  <div class="btn" style="left:601px;top:413px;width:114px;height:32px;font-size:11px">READ MORE</div>
</section>

<section class="abs testimonials">
  <h2 class="section-title">Testimonials</h2>
  <div class="rule" style="left:572px;top:106px"></div>
  <svg class="abs" style="left:82px;top:342px" width="16" height="20" viewBox="0 0 16 20"><path d="M11 2 3 10l8 8" stroke="#fff" stroke-width="2.5" fill="none"/></svg>
  <svg class="abs" style="left:1097px;top:342px" width="16" height="20" viewBox="0 0 16 20"><path d="m5 2 8 8-8 8" stroke="#fff" stroke-width="2.5" fill="none"/></svg>
  <div class="quote-card" style="left:132px"><div class="quote-mark">&ldquo;</div><p>There are many variations of passages of Lorem Ipsum available, but the majority have suffered alteration in some form, by injected humour, or randomised words which don't look even slightly believable. If you are going to use.</p><div class="rule"></div><cite>Daniel</cite></div>
  <div class="quote-card" style="left:454px"><div class="quote-mark">&ldquo;</div><p>There are many variations of passages of Lorem Ipsum available, but the majority have suffered alteration in some form, by injected humour, or randomised words which don't look even slightly believable. If you are going to use.</p><div class="rule"></div><cite>Daniel</cite></div>
  <div class="quote-card" style="left:775px"><div class="quote-mark">&ldquo;</div><p>There are many variations of passages of Lorem Ipsum available, but the majority have suffered alteration in some form, by injected humour, or randomised words which don't look even slightly believable. If you are going to use.</p><div class="rule"></div><cite>Daniel</cite></div>
</section>

<h2 class="section-title" style="top:2502px">Latest Articles</h2>
<svg class="abs" style="left:62px;top:2745px" width="40" height="16" viewBox="0 0 40 16"><path d="M39 8H2M9 1 2 8l7 7" stroke="#9a9a9a" stroke-width="1.5" fill="none"/></svg>
<svg class="abs" style="left:1092px;top:2745px" width="40" height="16" viewBox="0 0 40 16"><path d="M1 8h37M31 1l7 7-7 7" stroke="#9a9a9a" stroke-width="1.5" fill="none"/></svg>
<article class="article" style="left:132px">
  <div class="article-photo" role="img" aria-label="Couple smiling while reviewing documents with an advisor" style="background:linear-gradient(135deg,#7a6a5a,#d9c7b2 50%,#a89684)"></div>
  <div class="article-box">
    <h3>Lorem Ipsum is simply dummy text of the printing</h3>
    <p>There are many variations of passages of Lorem Ipsum available, but the majority have suffered alteration in some form, by injected humour, or randomised</p>
    <div class="btn" style="left:40px;top:190px;width:112px;height:32px;font-size:11px">READ MORE</div>
  </div>
</article>
<article class="article" style="left:616px">
  <div class="article-photo" role="img" aria-label="Clients talking with two advisors at a meeting table" style="background:linear-gradient(135deg,#4a4a52,#bfc2c6 50%,#6f6a66)"></div>
  <div class="article-box">
    <h3>Lorem Ipsum is simply dummy text of the printing</h3>
    <p>There are many variations of passages of Lorem Ipsum available, but the majority have suffered alteration in some form, by injected humour, or randomised</p>
    <div class="btn" style="left:40px;top:190px;width:112px;height:32px;font-size:11px">READ MORE</div>
  </div>
</article>

<h2 class="section-title" style="top:3159px">Our Video</h2>
<section class="abs video" role="img" aria-label="Overhead view of a team meeting around a white table with laptops">
  <svg class="play" width="64" height="64" viewBox="0 0 64 64"><circle cx="32" cy="32" r="29" fill="none" stroke="#b7b33a" stroke-width="4"/><path d="M25 19v26l20-13z" fill="#b7b33a"/></svg>
  <span>Play Video</span>
</section>

<section class="abs contact">
  <h2 class="section-title" style="top:60px">Contact Us</h2>
  <div class="rule" style="left:572px;top:112px"></div>
  <form class="form">
    <div class="field" style="left:31px;top:35px;width:246px;height:46px">Full Name</div>
    <div class="field" style="left:293px;top:35px;width:248px;height:46px">Email me</div>
    <div class="field" style="left:31px;top:100px;width:246px;height:47px">Phone</div>
    <div class="field" style="left:293px;top:100px;width:248px;height:47px">Subject</div>
    <div class="field" style="left:31px;top:167px;width:510px;height:123px">Message</div>
    <div class="btn" style="left:233px;top:317px;width:114px;height:34px">SUBMIT</div>
  </form>
</section>

<footer class="abs site-footer">
  <div class="brand" style="left:134px;top:60px">
    <div class="brand-mark"></div>
    <div class="brand-name">Vellmore</div>
  </div>
  <div class="btn" style="left:205px;top:166px;width:129px;height:34px;border-radius:8px;font-size:13px;color:var(--navy)">&#9679;&nbsp;LIVE CHAT</div>
  <h4 style="left:456px">MENU</h4>
  <ul class="menu-list"><li>HOME</li><li>ABOUT US</li><li>SERVICES</li><li>BLOG</li><li>TESTIMONIALS</li><li>CONTACT US</li></ul>
  <h4 style="left:656px">CONTACT US</h4>
  <div class="info" style="left:656px;top:88px"><span class="dot"><svg width="10" height="12" viewBox="0 0 10 12"><path d="M5 11S1 6.5 1 4a4 4 0 0 1 8 0c0 2.5-4 7-4 7z" fill="#03052e"/></svg></span><div>2150 Harbor Lane<br>Kent, WA 98032</div></div>
  <div class="info" style="left:656px;top:138px"><span class="dot"><svg width="11" height="11" viewBox="0 0 24 24"><path d="M5 3h4l2 5-2.5 1.5a11 11 0 0 0 6 6L16 13l5 2v4a2 2 0 0 1-2 2A16 16 0 0 1 3 5a2 2 0 0 1 2-2z" fill="#03052e"/></svg></span><div>Call Us<br>555.014.2290</div></div>
  <div class="info" style="left:656px;top:188px"><span class="dot"><svg width="12" height="9" viewBox="0 0 12 9"><rect x=".5" y=".5" width="11" height="8" fill="none" stroke="#03052e"/><path d="m.5.5 5.5 4 5.5-4" fill="none" stroke="#03052e"/></svg></span><div>E mail Us<br>info@vellmorefamilylaw.com</div></div>
  <h4 style="left:953px">FOLLOW US</h4>
  <div class="info" style="left:953px;top:88px"><span class="dot"></span><div>Like us on<br>CIRCLEBOOK</div></div>
  <div class="info" style="left:953px;top:138px"><span class="dot"></span><div>Follow us on<br>CHIRPER</div></div>
  <div class="info" style="left:953px;top:188px"><span class="dot"></span><div>Follow us on<br>WORKLINK</div></div>
</footer>
<div class="copyright">Copyright &copy; 2021 All Rights Reserved</div>

</body>
</html>
```